Fernhale Business Card Design

We are looking for a fresh business card design for our new logo. We would like a business card that is unique but friendly. We are in the window coverings business offering blinds, shutters and shades for homes.

Target Market(s)

Targeting the end-consumer

Industry/Entity Type

Business

Requirements
Must have
• Must have a dedicates space for a photo of our sales person. Must contain our new logo (attached).

```html
<!DOCTYPE html>
<html lang="en">
<head>
<meta charset="utf-8">
<title>Fernhale Business Cards</title>
<link href="https://fonts.googleapis.com/css2?family=Roboto+Condensed:wght@400;700&family=Roboto:wght@400&display=swap" rel="stylesheet">
<style>
  :root {
    --bg: #e9e6e1;
    --card: #fbfbfa;
    --ink: #6e6e6e;
    --ink-soft: #8c8c8c;
    --green: #8dc63f;
    --rule: #d8d8d8;
    --photo-top: #a9a9a9;
    --photo-bottom: #8f8f8f;
  }
  * { margin: 0; padding: 0; box-sizing: border-box; }
  html, body { width: 1200px; height: 886px; overflow: hidden; }
  body {
    background: var(--bg);
    position: relative;
    font-family: "Roboto Condensed", "Roboto", sans-serif;
    color: var(--ink);
  }
  .card {
    position: absolute;
    background: var(--card);
    box-shadow: 0 6px 18px rgba(0,0,0,0.18);
    overflow: hidden;
  }
  .card--front { left: 171px; top: 295px; width: 520px; height: 297px; }
  .card--back  { left: 731px; top: 183px; width: 297px; height: 520px; }

  .brand { display: flex; align-items: center; gap: 10px; }
  .brand__mark { width: 26px; height: 26px; background: var(--green); }
  .brand__name {
    font-family: "Roboto Condensed", sans-serif;
    font-weight: 400;
    font-size: 34px;
    color: var(--ink);
    letter-spacing: 0.5px;
  }

  .card--front .brand { position: absolute; left: 52px; top: 126px; }

  .divider {
    position: absolute;
    left: 262px; top: 28px;
    width: 1px; height: 241px;
    background: var(--rule);
  }

  .contact { position: absolute; left: 290px; top: 44px; }
  .contact__name {
    font-weight: 700; font-size: 19px; color: var(--green);
    letter-spacing: 0.3px; line-height: 1.1;
  }
  .contact__title { font-size: 13px; color: var(--ink-soft); margin-top: 2px; }
  .contact__address { font-size: 12.5px; line-height: 1.35; margin-top: 18px; }
  .contact__list { list-style: none; margin-top: 16px; font-size: 12.5px; line-height: 1.45; }
  .contact__list li { display: flex; align-items: center; gap: 8px; }
  .contact__list svg { width: 10px; height: 10px; flex: none; fill: var(--green); }

  .card--back .brand { position: absolute; left: 36px; top: 58px; }
  .card--back .brand__name { font-size: 32px; }
  .card--back .web {
    position: absolute; left: 38px; top: 104px;
    font-family: "Roboto", sans-serif;
    font-size: 11px; letter-spacing: 4.2px; color: var(--ink);
  }
  .photo {
    position: absolute; left: 70px; top: 220px; right: 0; bottom: 0;
    background: linear-gradient(180deg, var(--photo-top), var(--photo-bottom));
  }
</style>
</head>
<body>
  <section class="card card--front">
    <div class="brand">
      <span class="brand__mark"></span>
      <span class="brand__name">Fernhale</span>
    </div>
    <div class="divider"></div>
    <div class="contact">
      <p class="contact__name">JANE MARLOW</p>
      <p class="contact__title">CEO/FOUNDER</p>
      <p class="contact__address">4120 Willowbend Road<br>Cedar Falls, Oregon 97281</p>
      <ul class="contact__list">
        <li><svg viewBox="0 0 10 10"><path d="M2 0.5 L4 2.5 L3 4 Q4.5 6 6 7 L7.5 6 L9.5 8 L8 9.5 Q3 9 0.5 2 Z"/></svg>541 302 7716</li>
        <li><svg viewBox="0 0 10 10"><rect x="2.5" y="0" width="5" height="10" rx="1"/></svg>541 908 2245</li>
        <li><svg viewBox="0 0 10 10"><rect x="0.5" y="3" width="9" height="6"/><rect x="2.5" y="0.5" width="5" height="3"/></svg>541 667 3018</li>
        <li><svg viewBox="0 0 10 10"><rect x="0" y="1.5" width="10" height="7"/></svg>hello@fernhale.com</li>
        <li><svg viewBox="0 0 10 10"><circle cx="5" cy="5" r="5"/></svg>www.fernhale.com</li>
      </ul>
    </div>
  </section>

  <section class="card card--back">
    <div class="brand">
      <span class="brand__mark"></span>
      <span class="brand__name">Fernhale</span>
    </div>
    <p class="web">www.fernhale.com</p>
    <div class="photo" role="img" aria-label="Portrait photo of the salesperson"></div>
  </section>
</body>
</html>
```